TREVAL BUILDWORKS, LLC Webpage portfolio

I want to create a Website that allows my potential clients to browse my Skilled work via before and after photos. I want the website to enhance the work that I provide and potentially drive new business, or at least solidify my work.
I also do 3D CAD and Modeling of New Spaces and it would be nice to show some of that work from pencil design to 3D modeling, which I feel may help give me more clients.

The website needs to show a solid carpenter/company with the skills to get any project completed.

Types of Jobs - Custom Carpentry & Finishes, Kitchens, Baths, Basements, Decks, Porches, Whole House Renovation - Skilled Craftsmanship (Hardwood Flooring, Floor and Wall Tile) and much more...

Target Market(s)

Residential Home Renovation, Kitchen and Bath Renovation, Home Improvement

Industry/Entity Type

Residential Construction

Number of Pages Required

5+ page

Font styles to use
Sans Serif
Script

Requirements
Must have
• Similar to Plinvo.com, except for Treval Buildworks.
• Must be inviting.
• My Services Offered
• A way to reach me or contact me for estimates with some sort of Screening Questionare.
Nice to have
• Inviting Colors
Should not have
• Not sure at this time

```html
<!DOCTYPE html>
<html lang="en">
<head>
<meta charset="utf-8">
<title>Treval Buildworks — Design, Build &amp; Remodeling</title>
<link rel="stylesheet" href="https://fonts.googleapis.com/css2?family=Questrial&family=Open+Sans:wght@400;600&display=swap">
<style>
  :root{
    --navy:#0e4468;
    --navy-deep:#0b3b5c;
    --sky:#1ea0db;
    --bar:#1c8fcc;
    --ink:#1d2a35;
    --muted:#6c7680;
    --grey-band:#f5f5f5;
    --line:#e3e3e3;
    --white:#ffffff;
    --head:"Questrial", "Helvetica Neue", Arial, sans-serif;
    --body:"Open Sans", Arial, sans-serif;
  }
  *{box-sizing:border-box;margin:0;padding:0}
  html,body{width:1200px;height:3333px;overflow:hidden}
  body{position:relative;background:var(--white);font-family:var(--body);color:var(--ink)}
  .abs{position:absolute}
  .top-strip{left:0;top:0;width:1200px;height:10px;background:var(--sky)}

  /* header */
  .social{left:102px;top:72px;display:flex;gap:12px}
  .social span{width:18px;height:18px;background:var(--navy);border-radius:3px;display:block}
  .brand{left:0;width:1200px;top:58px;display:flex;justify-content:center;align-items:center;gap:12px}
  .brand-mark{width:26px;height:26px;background:var(--navy)}
  .brand-name{font-family:var(--head);font-size:38px;color:var(--navy);letter-spacing:.5px}
  .call{right:95px;top:62px;text-align:right;font-family:var(--head);color:var(--navy)}
  .call .label{font-size:21px}
  .call .phone{font-size:19px;margin-top:8px;display:flex;align-items:center;justify-content:flex-end;gap:8px}
  .nav{top:170px;left:0;width:1200px;display:flex;justify-content:center;gap:36px;font-family:var(--head);font-size:20px;color:var(--navy)}
  .nav a{color:inherit;text-decoration:none}
  .nav a.active{color:var(--sky)}

  /* hero */
  .hero{left:0;top:204px;width:1200px;height:545px;background:radial-gradient(ellipse at 50% 45%,#a0692c 0%,#5c3418 45%,#2b170b 100%)}
  .hero-title{top:390px;left:0;width:1200px;text-align:center;font-family:var(--head);font-size:41px;color:var(--white);letter-spacing:1px}
  .hero-text{top:452px;left:250px;width:700px;text-align:center;font-size:16px;line-height:24px;color:var(--white)}
  .btn-solid{left:467px;top:522px;width:262px;height:60px;background:var(--navy);color:var(--white);font-family:var(--head);font-size:18px;display:flex;align-items:center;justify-content:center;border-radius:3px}

  /* welcome */
  .welcome-title{left:98px;top:838px;font-family:var(--head);font-size:27px;color:var(--navy)}
  .welcome-sub{left:98px;top:886px;font-family:var(--head);font-size:18px;color:var(--ink)}
  .welcome-text{left:98px;top:922px;width:560px;font-size:12px;line-height:22px;color:var(--muted)}
  .btn-outline{display:flex;align-items:center;justify-content:center;border:1.5px solid var(--navy);color:var(--navy);font-family:var(--head);font-size:16px;background:var(--white)}
  .welcome-more{left:98px;top:1015px;width:175px;height:40px;font-size:18px}
  .welcome-photo{left:682px;top:776px;width:420px;height:317px;border:3px solid var(--navy);background:linear-gradient(160deg,#9c5a3c,#4a3024 60%,#1f2a33)}

  /* features */
  .feature{top:1160px;width:260px}
  .feature h3{font-family:var(--head);font-size:22px;color:var(--navy);font-weight:400;display:flex;align-items:center;gap:10px;height:36px}
  .feature .photo{margin-top:8px;height:163px;border-radius:4px}
  .feature p{margin-top:20px;font-size:12px;line-height:22px;color:var(--muted)}

  /* types */
  .types-band{left:0;top:1460px;width:1200px;height:813px;background:var(--grey-band)}
  .section-title{left:0;width:1200px;text-align:center;font-family:var(--head);font-size:27px;color:var(--navy)}
  .types-sub{top:1585px;left:290px;width:620px;text-align:center;font-size:12px;line-height:22px;color:var(--muted)}
  .job{width:311px;text-align:center}
  .job .icon{width:64px;height:50px;margin:0 auto;background:var(--navy);border-radius:4px;display:flex;align-items:center;justify-content:center}
  .job h4{margin-top:14px;font-family:var(--head);font-weight:400;font-size:21px;color:var(--navy)}
  .job p{margin:10px auto 0;width:230px;font-size:12px;line-height:22px;color:var(--muted)}
  .job .btn-outline{margin:14px auto 0;width:130px;height:33px;font-size:15px}
  .vline{width:1px;background:var(--line)}
  .hline{height:1px;background:var(--line)}
  .dots{top:2192px;left:0;width:1200px;display:flex;justify-content:center;gap:7px}
  .dots span{width:12px;height:12px;border-radius:50%;background:#b9bdc1}
  .dots span.on{background:var(--navy)}

  /* portfolio */
  .panel{top:2404px;width:491px;height:351px;border:3px solid var(--navy);display:flex}
  .panel .half{flex:1;position:relative}
  .panel .half span{position:absolute;left:14px;bottom:14px;font-family:var(--head);font-size:19px;color:var(--white);letter-spacing:1px}
  .panel .half.light span{color:var(--ink)}
  .arrow{top:2577px;width:24px;height:24px;background:#6f7d88;display:flex;align-items:center;justify-content:center}

  /* testimonial */
  .avatar{left:256px;top:2878px;width:146px;height:146px;border-radius:50%;background:radial-gradient(circle at 50% 40%,#8c99a3,#2c3a47)}
  .client{left:451px;top:2888px;font-family:var(--head);font-size:21px;color:var(--ink)}
  .quote{left:451px;top:2922px;width:535px;font-size:12px;line-height:19px;color:var(--ink)}

  /* footer */
  .footer{left:0;top:3062px;width:1200px;height:231px;background:var(--navy-deep)}
  .footer-brand{left:107px;top:3172px;display:flex;align-items:center;gap:10px}
  .footer-brand .brand-mark{background:var(--white);width:22px;height:22px}
  .footer-brand .brand-name{color:var(--white);font-size:30px}
  .fcol{top:3108px;color:var(--white)}
  .fcol h5{font-family:var(--head);font-weight:400;font-size:18px;letter-spacing:1px}
  .fcol ul{list-style:none;margin-top:18px;font-family:var(--head);font-size:14px;line-height:21px}
  .cards{left:916px;top:3180px;display:grid;grid-template-columns:repeat(3,58px);gap:28px 6px}
  .cards span{height:36px;border-radius:4px;background:#e9eef2}
  .cards span:nth-child(1){background:#8a4d9e}
  .cards span:nth-child(2){background:#f2c230}
  .cards span:nth-child(3){background:#ffffff}
  .bottom-bar{left:0;top:3293px;width:1200px;height:40px;background:var(--bar);display:flex;align-items:center;justify-content:center;font-family:var(--head);font-size:13px;color:var(--navy-deep)}
</style>
</head>
<body>
  <div class="abs top-strip"></div>

  <header>
    <div class="abs social" aria-label="Social links"><span></span><span></span><span></span></div>
    <div class="abs brand"><span class="brand-mark"></span><span class="brand-name">Treval Buildworks</span></div>
    <div class="abs call">
      <div class="label">Call Us Today</div>
      <div class="phone">
        <svg width="16" height="16" viewBox="0 0 16 16"><rect width="16" height="16" rx="3" fill="#0e4468"/><path d="M5 3.5l1.6 2.2-1 1c.6 1.3 1.6 2.3 2.8 2.9l1-1 2.2 1.5-.8 1.9C7.4 11.8 4.2 8.6 3.5 5z" fill="#fff"/></svg>
        1800 555 0142
      </div>
    </div>
    <nav class="abs nav">
      <a class="active">Home</a><a>About Us</a><a>Types of Jobs</a><a>Our Team</a><a>Get A Quote</a><a>Contact</a>
    </nav>
  </header>

  <section>
    <div class="abs hero" role="img" aria-label="Warm-lit luxury kitchen with dark wood cabinets and pendant lights"></div>
    <h1 class="abs hero-title">Make Your Home Look&nbsp; Luxurious</h1>
    <p class="abs hero-text">Lorem Ipsum is simply dummy text of the printing and typesetting industry. Lorem Ipsum has been the industry's standard dummy text ever since the 1500s</p>
    <div class="abs btn-solid">Get An Appointment</div>
  </section>

  <section>
    <h2 class="abs welcome-title">Welcome To TREVAL BUILDWORKS</h2>
    <div class="abs welcome-sub">Lorem Ipsum is simply</div>
    <p class="abs welcome-text">Lorem Ipsum is simply dummy text of the printing and typesetting industry. Lorem Ipsum has been the industry's standard dummy text ever since the 1500s, when an unknown printer took a galley of type and scrambled it to make a type.</p>
    <div class="abs btn-outline welcome-more">MORE</div>
    <div class="abs welcome-photo" role="img" aria-label="Finished living room with stone fireplace and built-in shelving"></div>
  </section>

  <section>
    <div class="abs feature" style="left:142px">
      <h3><svg width="26" height="26" viewBox="0 0 26 26"><path d="M2 2h8L7 5l4 4-2 2-4-4-3 3zM24 2v8l-3-3-4 4-2-2 4-4-3-3zM2 24v-8l3 3 4-4 2 2-4 4 3 3zM24 24h-8l3-3-4-4 2-2 4 4 3-3z" fill="#0e4468"/></svg>Modern Design</h3>
      <div class="photo" role="img" aria-label="Modern kitchen with granite island" style="background:linear-gradient(150deg,#b06a35,#5a2f18)"></div>
      <p>Lorem Ipsum is simply dummy text of the printing and typesetting industry.</p>
    </div>
    <div class="abs feature" style="left:469px">
      <h3><svg width="24" height="26" viewBox="0 0 24 26"><path d="M12 1l11 6v12l-11 6-11-6V7z" fill="#0e4468"/></svg>High Quality</h3>
      <div class="photo" role="img" aria-label="New porch with white railings and steps" style="background:linear-gradient(160deg,#b7b2a4,#6e6a5c 60%,#4b5a3e)"></div>
      <p>Lorem Ipsum is simply dummy text of the printing and typesetting industry.</p>
    </div>
    <div class="abs feature" style="left:793px">
      <h3><svg width="26" height="26" viewBox="0 0 26 26"><circle cx="13" cy="13" r="9" fill="#0e4468"/><g stroke="#0e4468" stroke-width="4"><path d="M13 1v24M1 13h24M4.5 4.5l17 17M21.5 4.5l-17 17"/></g><circle cx="13" cy="13" r="4" fill="#fff"/></svg>Quick Support</h3>
      <div class="photo" role="img" aria-label="Gloved hand cleaning a kitchen counter" style="background:linear-gradient(160deg,#c9d2de,#8a98ad 60%,#c86a6a)"></div>
      <p>Lorem Ipsum is simply dummy text of the printing and typesetting industry.</p>
    </div>
  </section>

  <section>
    <div class="abs types-band"></div>
    <h2 class="abs section-title" style="top:1536px">Types Of Job</h2>
    <p class="abs types-sub">Lorem Ipsum is simply dummy text of the printing and typesetting industry. Lorem Ipsum has been the industry's standard dummy text ever since the 1500s.</p>

    <div class="abs vline" style="left:440px;top:1660px;height:505px"></div>
    <div class="abs vline" style="left:751px;top:1660px;height:505px"></div>
    <div class="abs hline" style="left:96px;top:1915px;width:1015px"></div>

    <div class="abs job" style="left:129px;top:1686px">
      <div class="icon"><svg width="34" height="26" viewBox="0 0 34 26"><path d="M3 12h28v4a6 6 0 0 1-6 6H9a6 6 0 0 1-6-6z M6 12V4a3 3 0 0 1 6 0" fill="none" stroke="#fff" stroke-width="2.5"/><path d="M3 12h28v4a6 6 0 0 1-6 6H9a6 6 0 0 1-6-6z" fill="#fff"/></svg></div>
      <h4>Baths</h4><p>Lorem Ipsum is simply dummy text of the printing and typesetting industry.</p><div class="btn-outline">MORE</div>
    </div>
    <div class="abs job" style="left:440px;top:1686px">
      <div class="icon"><svg width="32" height="28" viewBox="0 0 32 28"><path d="M16 2L2 14h4v12h8v-8h4v8h8V14h4z" fill="#fff"/></svg></div>
      <h4>House Renovation</h4><p>Lorem Ipsum is simply dummy text of the printing and typesetting industry.</p><div class="btn-outline">MORE</div>
    </div>
    <div class="abs job" style="left:751px;top:1686px">
      <div class="icon"><svg width="30" height="30" viewBox="0 0 30 30"><circle cx="9" cy="11" r="6" fill="#fff"/><circle cx="21" cy="11" r="6" fill="#fff"/><circle cx="15" cy="8" r="6" fill="#fff"/><rect x="8" y="13" width="14" height="13" fill="#fff"/></svg></div>
      <h4>Kitchens</h4><p>Lorem Ipsum is simply dummy text of the printing and typesetting industry.</p><div class="btn-outline">MORE</div>
    </div>

    <div class="abs job" style="left:129px;top:1958px">
      <div class="icon"><svg width="34" height="26" viewBox="0 0 34 26"><path d="M3 3h28v12H3z M6 15v9M28 15v9M3 8h28" fill="none" stroke="#fff" stroke-width="2.5"/></svg></div>
      <h4>Decks</h4><p>Lorem Ipsum is simply dummy text of the printing and typesetting industry.</p><div class="btn-outline">MORE</div>
    </div>
    <div class="abs job" style="left:440px;top:1958px">
      <div class="icon"><svg width="30" height="28" viewBox="0 0 30 28"><path d="M5 20a10 10 0 0 1 20 0z" fill="#fff"/><rect x="2" y="21" width="26" height="4" fill="#fff"/><rect x="13" y="4" width="4" height="6" fill="#fff"/></svg></div>
      <h4>Carpentry &amp; Finishes</h4><p>Lorem Ipsum is simply dummy text of the printing and typesetting industry.</p><div class="btn-outline">MORE</div>
    </div>
    <div class="abs job" style="left:751px;top:1958px">
      <div class="icon"><svg width="30" height="28" viewBox="0 0 30 28"><path d="M2 26h26V2h-6v6h-6v6h-6v6H4z" fill="#fff"/></svg></div>
      <h4>Basements</h4><p>Lorem Ipsum is simply dummy text of the printing and typesetting industry.</p><div class="btn-outline">MORE</div>
    </div>

    <div class="abs dots"><span class="on"></span><span></span><span></span><span></span></div>
  </section>

  <section>
    <h2 class="abs section-title" style="top:2330px">Our Portfolio</h2>
    <div class="abs arrow" style="left:41px"><svg width="12" height="12" viewBox="0 0 12 12"><path d="M8 1L3 6l5 5" fill="none" stroke="#fff" stroke-width="2"/></svg></div>
    <div class="abs arrow" style="left:1130px"><svg width="12" height="12" viewBox="0 0 12 12"><path d="M4 1l5 5-5 5" fill="none" stroke="#fff" stroke-width="2"/></svg></div>
    <div class="abs panel" style="left:96px">
      <div class="half" role="img" aria-label="Kitchen before renovation" style="background:linear-gradient(170deg,#8a7a5a,#c7b179 60%,#d9cfa8)"><span>BEFORE</span></div>
      <div class="half" role="img" aria-label="Kitchen after renovation" style="background:linear-gradient(170deg,#5e6a50,#8f9a7e 50%,#5f7a78)"><span>AFTER</span></div>
    </div>
    <div class="abs panel" style="left:611px">
      <div class="half light" role="img" aria-label="Pencil design drawing of a curved kitchen island" style="background:linear-gradient(170deg,#ffffff,#ececec)"><span>PENCIL DESIGN</span></div>
      <div class="half" role="img" aria-label="Original kitchen space" style="background:linear-gradient(170deg,#b39070,#7a5840 55%,#c9c2b8)"><span>ORIGINAL</span></div>
    </div>
  </section>

  <section>
    <h2 class="abs section-title" style="top:2812px;color:var(--navy)">TESTIMONIALS</h2>
    <div class="abs avatar" role="img" aria-label="Client portrait"></div>
    <div class="abs client">Client Name</div>
    <p class="abs quote">Lorem Ipsum is simply dummy text of the printing and typesetting industry. Lorem Ipsum has been the industry's standard dummy text ever since the 1500s, when an unknown printer took a galley Lorem Ipsum is simply dummy text of the printing and typesetting industry. Lorem Ipsum has been the industry's standard dummy.</p>
  </section>

  <footer>
    <div class="abs footer"></div>
    <div class="abs footer-brand"><span class="brand-mark"></span><span class="brand-name">Treval Buildworks</span></div>
    <div class="abs fcol" style="left:467px">
      <h5>SITE MAP</h5>
      <ul><li>Home</li><li>About Us</li><li>Type Of Job</li><li>Team</li><li>Contact Us</li></ul>
    </div>
    <div class="abs fcol" style="left:658px">
      <h5>HELP</h5>
      <ul><li>Privacy Policy</li><li>Help/FAQ</li><li>Policy/Terms &amp; Conditions</li></ul>
    </div>
    <div class="abs fcol" style="left:916px;top:3112px"><h5>PAYMENT</h5></div>
    <div class="abs cards" aria-label="Accepted payment methods"><span></span><span></span><span></span><span></span><span></span><span></span></div>
    <div class="abs bottom-bar">© 2017 Treval Buildworks. All Rights Reserved.</div>
  </footer>
</body>
</html>
```